Dovecote Realty

Business cards for 4 people

They need to say for all
87 Tarrow Quay, Boston MA 02114

Each person will have their own personal information
We would like gold embossing for the name of the company
Marla is the blonde sitting in the chair smiling her information should be on the back of the card with her name and information
Should say for slogan classic pattern, elevated experience
grace@dovecoteprops.com
(413) 555-0182

Odette is the brunette with wavy hair in the tan suit odette@dovecoteprops.com
(617) 555-0137

faith@dovecoteprops.com
(413) 555-0164
standing next to the chair

hope@dovecoteprops.com
(413) 555-0199
close up headshot

```html
<!DOCTYPE html>
<html lang="en">
<head>
<meta charset="utf-8">
<title>Dovecote Realty – Business Card</title>
<link href="https://fonts.googleapis.com/css2?family=Open+Sans:wght@400;600;700&display=swap" rel="stylesheet">
<style>
  :root {
    --backdrop: #e4ddd3;
    --navy-light: #2a3b58;
    --navy: #17243d;
    --navy-deep: #0f1a2e;
    --gold: #d39a4c;
    --gold-text: #c89458;
    --name-cream: #d9cab6;
    --title-tan: #c8a47c;
    --photo-light: #e6dccd;
    --photo-tan: #a87a52;
  }
  * { margin: 0; padding: 0; box-sizing: border-box; }
  html, body {
    width: 1200px; height: 1046px; overflow: hidden;
    background: var(--backdrop);
    font-family: "Open Sans", Arial, sans-serif;
  }
  .card {
    position: absolute; left: 50px; top: 221px;
    width: 1100px; height: 604px; border-radius: 30px; overflow: hidden;
    background:
      radial-gradient(ellipse at 15% 95%, rgba(70,90,125,.45), transparent 45%),
      radial-gradient(ellipse at 10% 5%, rgba(70,90,125,.5), transparent 40%),
      linear-gradient(120deg, var(--navy-light) 0%, var(--navy) 40%, var(--navy-deep) 70%, var(--navy) 100%);
  }
  .brand {
    position: absolute; left: 41px; top: 36px; width: 308px;
    display: flex; flex-direction: column; align-items: center;
    color: var(--gold-text); font-weight: 600;
  }
  .brand-circle {
    width: 104px; height: 104px; border-radius: 50%;
    border: 3px solid var(--gold-text); margin-bottom: 8px;
  }
  .brand-name { font-size: 44px; letter-spacing: 4px; line-height: 1; }
  .brand-sub { font-size: 14px; letter-spacing: 12px; margin-top: 6px; padding-left: 12px; line-height: 1; }
  .name-band {
    position: absolute; left: 0; top: 252px; width: 660px; height: 94px;
    background: linear-gradient(90deg, #c98f48 0%, rgba(150,110,70,.75) 6%, rgba(100,78,62,.6) 45%, rgba(23,36,61,0) 100%);
  }
  .person-name {
    position: absolute; left: 41px; top: 255px;
    font-size: 49px; font-weight: 700; color: var(--name-cream); line-height: 1.1;
  }
  .person-title {
    position: absolute; left: 41px; top: 313px;
    font-size: 20px; font-weight: 600; color: var(--title-tan);
  }
  .address {
    position: absolute; left: 41px; top: 374px;
    font-size: 27px; line-height: 36px; color: var(--gold-text); letter-spacing: .5px;
  }
  .contacts { position: absolute; left: 40px; top: 466px; list-style: none; }
  .contacts li {
    display: flex; align-items: center; height: 36.5px;
    font-size: 27px; color: var(--gold-text); letter-spacing: .3px;
  }
  .contacts svg { width: 26px; height: 26px; margin-right: 14px; flex: none; }
  .portrait {
    position: absolute; left: 644px; top: 97px; width: 418px; height: 418px;
    border-radius: 50%; border: 6px solid var(--gold);
    background: radial-gradient(circle at 55% 60%, var(--photo-tan) 0%, #8a6242 35%, var(--photo-light) 62%);
  }
</style>
</head>
<body>
  <div class="card">
    <div class="brand">
      <div class="brand-circle"></div>
      <div class="brand-name">DOVECOTE</div>
      <div class="brand-sub">REALTY</div>
    </div>

    <div class="name-band"></div>
    <div class="person-name">Odette Marchand</div>
    <div class="person-title">Real Estate Advisor and Sales Manager</div>

    <div class="address">87 Tarrow Quay,<br>Boston MA 02114</div>

    <ul class="contacts">
      <li>
        <svg viewBox="0 0 24 24" fill="none" stroke="currentColor" stroke-width="2" stroke-linecap="round" stroke-linejoin="round"><path d="M22 16.9v3a2 2 0 0 1-2.2 2 19.8 19.8 0 0 1-8.6-3.1 19.5 19.5 0 0 1-6-6A19.8 19.8 0 0 1 2.1 4.2 2 2 0 0 1 4.1 2h3a2 2 0 0 1 2 1.7c.1 1 .4 1.9.7 2.8a2 2 0 0 1-.5 2.1L8 9.9a16 16 0 0 0 6 6l1.3-1.3a2 2 0 0 1 2.1-.4c.9.3 1.8.6 2.8.7a2 2 0 0 1 1.8 2z"/></svg>
        (617) 555-0137
      </li>
      <li>
        <svg viewBox="0 0 24 24" fill="none" stroke="currentColor" stroke-width="2"><circle cx="12" cy="12" r="10"/><path d="M2 12h20M12 2a15 15 0 0 1 0 20M12 2a15 15 0 0 0 0 20"/></svg>
        www.dovecoteprops.com
      </li>
      <li>
        <svg viewBox="0 0 24 24" fill="none" stroke="currentColor" stroke-width="2" stroke-linejoin="round"><rect x="2" y="5" width="20" height="15" rx="2"/><path d="M2 7l10 7 10-7"/></svg>
        odette@dovecoteprops.com
      </li>
    </ul>

    <div class="portrait" role="img" aria-label="Portrait photo of Odette, brunette with wavy hair in a tan suit"></div>
  </div>
</body>
</html>
```